Branding Guide and Website for Q7Systems

Need an experienced Graphics Designer with a proven track record to create a design and branding guide for all media formats. From this guide you will then create a new website design for Q7systems.com.
There will be 8 pages (to start) with the new website. Each page will have multiple features and panels each need to have individual attention and customization that collectively fit together into a single cohesive look and feel.
We have not been able to get good designs I’m attaching one version which is the best we’ve received which is not bad but needs to be polished up better and the images need to change. I’d like to have some other accent colors but not too much I like the white, dark blue, gray, dark gray style.
Here are some sites that I like –
http://www.brelvant.com/
https://www.vontaric.com/ (layout good, graphics not great)
http://www.glastrek.com/ (good layout and graphics, too much animation)
https://www.pendrowix.com/ (a little boring but the colors and some of the top images are good)
https://www.tarnowelk.com/ (a little over the top colors are off but they have some good info graphics)
We don’t expect you will code the site however if you have that capability we’ll need it responsive/flat for mobile. Otherwise we can find someone to do the programming and we’ll just need the design files and images.
Branding guide will be used for web, email, print etc. so you’ll need to consider all guidelines for all formats. That is about it let me know if any questions we can have a call to discuss further if it is easier.
Not sure why they want a minimum of 300 words I’m done now but apparently have to keep typing so that is what I’m doing and Ok I’m at 300 words, almost there and we’re here now.

Target Market(s)

Customers looking for IT Services, Private Cloud, Security Services, Advanced Support, Fully Managed or Co-Managed IT.

Industry/Entity Type

It Company

Number of Pages Required

5+ page

Font styles to use
Sans Serif

Colors
0255a3
959595
e6e6e6
ffffff

Requirements
Must have
• Clean, professional and modern look using iconography, info graphics, flat etc.

```html
<!DOCTYPE html>
<html lang="en">
<head>
<meta charset="utf-8">
<title>Q7 Systems — IT Service Excellence</title>
<link href="https://fonts.googleapis.com/css2?family=Open+Sans:wght@400;600;700;800&display=swap" rel="stylesheet">
<style>
:root{
  --blue:#0255a3;
  --blue-light:#2e9fe0;
  --blue-sky:#5cc2f2;
  --gray:#959595;
  --gray-light:#e6e6e6;
  --gray-bg:#f3f3f3;
  --dark:#333333;
  --footer:#2b2b2b;
  --footer-deep:#1f1f1f;
  --white:#ffffff;
  --orange:#f5a623;
  --text:#666666;
}
*{margin:0;padding:0;box-sizing:border-box}
html,body{width:1200px;height:2704px;overflow:hidden}
body{font-family:"Open Sans",Arial,sans-serif;color:var(--text);background:var(--white);font-size:13px;line-height:1.6}
.section-title{font-size:24px;font-weight:800;color:var(--dark);text-align:center;text-transform:uppercase;letter-spacing:.5px}
.title-rule{width:50px;height:3px;background:var(--blue);margin:10px auto 0}
.lead{max-width:560px;margin:16px auto 0;text-align:center;font-size:12px;color:var(--gray)}

/* nav */
.site-nav{height:88px;display:flex;align-items:center;justify-content:space-between;padding:0 40px;background:var(--white);border-bottom:1px solid var(--gray-light)}
.brand{display:flex;align-items:center;gap:10px;font-size:22px;font-weight:800;color:var(--blue)}
.brand-mark{width:22px;height:22px;background:var(--blue);border-radius:50%}
.menu{display:flex;list-style:none;gap:4px}
.menu li{font-size:11px;font-weight:600;text-transform:uppercase;color:var(--gray);padding:10px 14px}
.menu li.active{background:var(--blue);color:var(--white)}

/* hero */
.hero{height:504px;position:relative;background:linear-gradient(180deg,var(--blue-light),var(--blue-sky));overflow:hidden}
.hero-copy{position:absolute;left:70px;top:160px;color:var(--white)}
.hero-copy h1{font-size:40px;font-weight:800;letter-spacing:.5px}
.hero-copy p{font-size:15px;margin-top:4px}
.btn{display:inline-block;font-size:11px;font-weight:700;text-transform:uppercase;padding:14px 26px;color:var(--white)}
.btn-orange{background:var(--orange);margin-top:30px}
.btn-blue{background:var(--blue)}
.hero-art{position:absolute;right:110px;top:40px;width:560px;height:420px;border-radius:8px;background:radial-gradient(ellipse at center,rgba(255,255,255,.55),rgba(255,255,255,.08) 70%)}
.slide-arrow{position:absolute;top:220px;width:34px;height:64px;background:rgba(0,40,90,.45);display:flex;align-items:center;justify-content:center}
.slide-arrow.left{left:0}.slide-arrow.right{right:0}

/* services */
.services{height:498px;background:var(--gray-bg);padding-top:48px}
.service-grid{display:grid;grid-template-columns:repeat(3,300px);column-gap:70px;row-gap:46px;justify-content:center;margin-top:44px}
.service{display:flex;gap:16px}
.service svg{flex:none}
.service h3{font-size:15px;font-weight:700;color:var(--dark)}
.service p{font-size:11px;color:var(--gray);line-height:1.5;margin-top:4px}

/* help */
.help{height:590px;padding-top:40px}
.help-grid{display:grid;grid-template-columns:repeat(4,240px);gap:30px;justify-content:center;margin-top:34px}
.help-card{text-align:center}
.help-photo{height:160px}
.help-card h3{font-size:15px;font-weight:700;color:var(--dark);margin-top:14px}
.help-card p{font-size:11px;color:var(--gray);line-height:1.5;margin-top:4px}
.clients-note{text-align:center;font-size:11px;color:var(--gray);margin-top:30px}
.clients-note b{color:var(--blue)}
.clients{display:flex;justify-content:center;gap:70px;margin-top:24px}
.client{display:flex;align-items:center;gap:8px;font-size:22px;font-weight:700;color:#8a8a8a}
.client i{width:18px;height:18px;background:#8a8a8a;border-radius:50%;display:block}

/* testimonials */
.testimonials{height:390px;background:var(--gray-bg);padding-top:58px}
.quote-grid{display:grid;grid-template-columns:repeat(3,320px);gap:40px;justify-content:center;margin-top:44px}
.quote{text-align:center;font-size:12px;font-style:italic;color:var(--gray);line-height:1.6}
.quote cite{display:block;margin-top:16px;font-style:italic;color:var(--blue);font-weight:600}

/* different */
.different{height:374px;position:relative;padding-top:50px}
.different .lead{max-width:520px}
.different .cta{text-align:center;margin-top:34px}
.mascot{position:absolute;right:60px;top:30px;width:150px;height:330px;border-radius:60px 60px 10px 10px;background:linear-gradient(180deg,#8fb8d8,#e6e6e6)}

/* footer */
.site-footer{height:260px;background:var(--footer);color:#bdbdbd;display:grid;grid-template-columns:260px 260px 260px 220px;gap:40px;padding:40px 60px 0}
.site-footer h4{color:var(--white);font-size:14px;font-weight:600;margin-bottom:14px}
.site-footer p,.site-footer li{font-size:11px;line-height:1.9}
.social{display:flex;gap:8px;margin-bottom:16px}
.social span{width:26px;height:26px;border:2px solid #bdbdbd;border-radius:50%}
.field{height:28px;background:var(--white);margin-bottom:10px;font-size:11px;color:var(--gray);padding:6px 10px}
.btn-submit{background:var(--blue);color:var(--white);font-size:10px;font-weight:700;padding:7px 16px;display:inline-block}
.browse{list-style:none}
.browse li::before{content:"›";color:var(--blue-light);margin-right:8px}
</style>
</head>
<body>

<header class="site-nav">
  <div class="brand"><span class="brand-mark"></span>Q7 Systems</div>
  <ul class="menu">
    <li class="active">Home</li><li>Managed Services</li><li>Corporate Cloud</li><li>Cloud Solutions</li><li>Support Services</li><li>Sevices</li><li>Company</li>
  </ul>
</header>

<section class="hero">
  <div class="hero-art" role="img" aria-label="Illustration of a cloud connected to devices: desktop, laptop, phone, tablet and servers"></div>
  <div class="hero-copy">
    <h1>IT SERVICE EXCELLENCE</h1>
    <p>Striving for Continuous Service Improvement for Our Clients</p>
    <span class="btn btn-orange">Get Started Now</span>
  </div>
  <div class="slide-arrow left"><svg width="12" height="20"><path d="M10 2 2 10l8 8" fill="none" stroke="#fff" stroke-width="2.5"/></svg></div>
  <div class="slide-arrow right"><svg width="12" height="20"><path d="M2 2l8 8-8 8" fill="none" stroke="#fff" stroke-width="2.5"/></svg></div>
</section>

<section class="services">
  <h2 class="section-title">What We Do</h2>
  <div class="title-rule"></div>
  <p class="lead">Providing Q7 Systems IT solutions to businesses of every size, with trusted support and expert service delivered across all of your IT needs.</p>
  <div class="service-grid">
    <div class="service">
      <svg width="40" height="40" viewBox="0 0 40 40" fill="none" stroke="#0255a3" stroke-width="2.5"><path d="M8 32 24 16"/><circle cx="28" cy="12" r="7"/><path d="M6 8l8 8M10 6l-4 4"/></svg>
      <div><h3>Managed Services</h3><p>We provide comprehensive technology management, IT services and support, whether you need a full team.</p></div>
    </div>
    <div class="service">
      <svg width="40" height="40" viewBox="0 0 40 40" fill="none" stroke="#0255a3" stroke-width="2.5"><path d="M10 28a7 7 0 0 1 1-14 9 9 0 0 1 17 2 6 6 0 0 1 1 12z"/></svg>
      <div><h3>Private Cloud</h3><p>We set systems and applications into a cloud made to match your performance and business needs.</p></div>
    </div>
    <div class="service">
      <svg width="40" height="40" viewBox="0 0 40 40" fill="none" stroke="#0255a3" stroke-width="2.5"><rect x="9" y="18" width="22" height="16" rx="2"/><path d="M14 18v-5a6 6 0 0 1 12 0v5"/></svg>
      <div><h3>Security Services</h3><p>To prevent breaches and proactively protect, we build layers of security to defend data.</p></div>
    </div>
    <div class="service">
      <svg width="40" height="40" viewBox="0 0 40 40" fill="none" stroke="#0255a3" stroke-width="2.5"><path d="M8 24v-4a12 12 0 0 1 24 0v4"/><rect x="6" y="22" width="6" height="10" rx="2"/><rect x="28" y="22" width="6" height="10" rx="2"/></svg>
      <div><h3>Advanced Support</h3><p>Get in touch with expert help when you need it, with a team that knows your business.</p></div>
    </div>
    <div class="service">
      <svg width="40" height="40" viewBox="0 0 40 40" fill="none" stroke="#0255a3" stroke-width="2.5"><rect x="15" y="5" width="10" height="8"/><rect x="4" y="28" width="10" height="8"/><rect x="26" y="28" width="10" height="8"/><path d="M20 13v8M9 28v-7h22v7"/></svg>
      <div><h3>Network Services</h3><p>Every organization needs a reliable network to connect teams, systems and customers.</p></div>
    </div>
    <div class="service">
      <svg width="40" height="40" viewBox="0 0 40 40" fill="none" stroke="#0255a3" stroke-width="2.5"><path d="M32 20a12 12 0 1 1-4-9"/><path d="M29 5v7h-7"/></svg>
      <div><h3>Disaster Recovery</h3><p>Every business requires disaster recovery solutions to mitigate and adapt to any unplanned event.</p></div>
    </div>
  </div>
</section>

<section class="help">
  <h2 class="section-title">How Can We Help Your Business?</h2>
  <div class="title-rule"></div>
  <p class="lead">Our complete managed service approach lets us provide complete service and technology management, allowing you to focus on what matters most in business.</p>
  <div class="help-grid">
    <div class="help-card"><div class="help-photo" role="img" aria-label="Photo of a glowing world network" style="background:linear-gradient(135deg,#0a3a6b,#2e9fe0)"></div><h3>Your Network</h3><p>A complete network of solutions, connectivity and total security.</p></div>
    <div class="help-card"><div class="help-photo" role="img" aria-label="Photo of hands typing on a laptop" style="background:linear-gradient(135deg,#c9c9c9,#6d6d6d)"></div><h3>Your Web Presence</h3><p>Grow your web presence through the marketing of your site.</p></div>
    <div class="help-card"><div class="help-photo" role="img" aria-label="Photo of code on a computer screen" style="background:linear-gradient(135deg,#2a1a12,#c0703a)"></div><h3>Your Applications</h3><p>Website designed to integrate with all the tools of your business.</p></div>
    <div class="help-card"><div class="help-photo" role="img" aria-label="Photo of a technician working in a server room" style="background:linear-gradient(135deg,#e9eef3,#7f93a8)"></div><h3>Your Piece of Mind</h3><p>Partner with us for the peace of strategy and proactive IT support.</p></div>
  </div>
  <p class="clients-note">Start your journey with us and join many great companies that already trust <b>Q7 Systems</b>.</p>
  <div class="clients">
    <div class="client"><i></i>Vantle</div>
    <div class="client"><i></i>Orbiqa</div>
    <div class="client">Lumigrain</div>
    <div class="client">Framewell</div>
    <div class="client"><i style="border-radius:0"></i>Tessaro</div>
  </div>
</section>

<section class="testimonials">
  <h2 class="section-title">What Are People Saying About Q7 Systems</h2>
  <div class="title-rule"></div>
  <div class="quote-grid">
    <blockquote class="quote">“Their team responds quickly and keeps our systems running without a hitch. We finally have IT we never worry about, and our staff can focus on serving clients every single day.”<cite>Alex Mercer, City Name</cite></blockquote>
    <blockquote class="quote">“Moving to their private cloud was smooth from start to finish. Clear planning, honest advice and steady support made the change easy for our whole office.”<cite>Alex Mercer, City Name</cite></blockquote>
    <blockquote class="quote">“Security used to keep me up at night. Now we have layered protection, regular reports and a partner who explains every step in plain language.”<cite>Alex Mercer, City Name</cite></blockquote>
  </div>
</section>

<section class="different">
  <h2 class="section-title">We Are Different</h2>
  <div class="title-rule"></div>
  <p class="lead">We bring practical expertise and genuine care to every client, blending proactive monitoring, honest guidance and responsive people so your technology simply works and your business keeps moving forward.</p>
  <div class="cta"><span class="btn btn-blue">How It Works</span></div>
  <div class="mascot" role="img" aria-label="Illustration of a cartoon IT technician character"></div>
</section>

<footer class="site-footer">
  <div>
    <div class="social"><span></span><span></span><span></span><span></span></div>
    <p>© 2016 Q7 Systems Inc.<br>All Rights Reserved<br>Privacy Policy</p>
  </div>
  <div>
    <h4>Contact us</h4>
    <p>2450 Harbor Lane, Suite 104<br>Fairview, CA 90000<br>1-800-555-0142<br>hello@q7systems.com</p>
  </div>
  <div>
    <h4>Newsletter</h4>
    <div class="field">Name</div>
    <div class="field">Email address</div>
    <span class="btn-submit">SUBMIT</span>
  </div>
  <div>
    <h4>Browse</h4>
    <ul class="browse"><li>Managed Services</li><li>Private Cloud</li><li>Security Services</li><li>Network Services</li><li>Disaster Recovery</li></ul>
  </div>
</footer>

</body>
</html>
```